New website design and logo for FlintBoro.com to help ignite the website sales.

Hi designers,

Flintboro is a new welding brand that is selling welding equipement.

Currently I have around 5 to 10 products. The issue is that the site itself does not do that much of sales. So I have to do something about the seo etc. but that is out of scope for the design.

What is in scope is to comeup with a new logo and website look and feel that is in line with the customers.

men, non professionals, garage, home improvements, perhaps sme ( small mediul entreprice business that want to start in the welding industry.

Products are midrange prices and quality. The look and feel must breath cool stuff, sexy ( women in working cloths carrying welding gloves, other protection gear and weldels)

The wedsite is build in wordpress with the Kora theme. I am an IT guy myself withhout any creativity in me :( so if you can help me with that that would be great.

Please have a quick look at flintboro.com

Best regards,
Joris

Target Market(s)

non professional welders that do metal work in there garage

Coding

Coded - Design and coding required

Number of Pages Required

3 page

Font styles to use
Sans Serif

Colors
0355a3
ffc214

Requirements
Must have
• I would like to see a new homepage and product page design together with a new logo.
Nice to have
• shop design

```html
<!DOCTYPE html>
<html lang="en">
<head>
<meta charset="utf-8">
<title>Flintboro – Welding Equipment</title>
<link rel="stylesheet" href="https://fonts.googleapis.com/css2?family=Roboto:wght@400;500;700;900&display=swap">
<style>
:root{
  --blue:#0d5cc6;
  --blue-light:#a9cbee;
  --orange:#fba61b;
  --ink:#1f1f1f;
  --text:#3a3a3a;
  --grey-bg:#efefef;
  --dark:#1c1f24;
  --darker:#15171b;
  --white:#ffffff;
}
*{box-sizing:border-box;margin:0;padding:0}
html,body{width:1200px;height:3723px;overflow:hidden}
body{position:relative;font-family:'Roboto',Arial,sans-serif;color:var(--text);background:var(--white)}
.abs{position:absolute}
a{color:inherit;text-decoration:none}

/* header */
.hero-art{position:absolute;left:0;top:0;width:1200px;height:700px}
.topbar{position:absolute;left:0;top:0;width:1200px;height:40px}
.topbar .contact{position:absolute;top:12px;font-size:13px;color:var(--ink);display:flex;align-items:center;gap:5px}
.search{position:absolute;left:714px;top:0;width:237px;height:40px;background:#e2e2e2;font-size:11px;color:#777;padding:12px 0 0 14px}
.search svg{position:absolute;right:12px;top:12px}
.user-tools{position:absolute;left:996px;top:12px;display:flex;gap:8px;font-size:13px;color:var(--ink);align-items:center}
.brand{position:absolute;display:flex;align-items:center;gap:8px;font-weight:700;letter-spacing:.5px}
.brand .dot{width:16px;height:16px;border-radius:50%;background:var(--orange)}
.main-nav{position:absolute;top:74px;left:0;font-size:14px;font-weight:700;color:var(--white)}
.main-nav a{position:absolute;white-space:nowrap}
.btn{position:absolute;display:flex;align-items:center;justify-content:center;background:var(--orange);color:var(--white);font-weight:700;border-radius:24px;box-shadow:0 0 0 3px rgba(251,166,27,.35)}
.hero-title{position:absolute;left:111px;top:214px;width:620px;font-size:45px;line-height:64px;font-weight:700;color:var(--white)}
.slider-dots span{position:absolute;left:1096px;width:8px;height:8px;border-radius:50%;background:var(--white)}
.slider-dots span.on{background:var(--orange);width:10px;height:10px;left:1095px}

/* section titles */
.section-title{position:absolute;left:0;width:1200px;text-align:center;font-size:32px;font-weight:700;letter-spacing:.2px}
.section-title .o{color:var(--orange)}
.section-title .b{color:var(--blue)}
.rule{position:absolute;width:46px;height:3px;background:var(--orange)}

/* products */
.shipping{position:absolute;left:0;top:836px;width:1200px;text-align:center;font-size:16px;color:var(--orange);font-weight:500}
.product-card{position:absolute;top:896px;width:233px;height:298px;background:var(--white);border-radius:10px;box-shadow:0 2px 12px rgba(0,0,0,.16);overflow:hidden}
.product-card .photo{position:absolute;left:12px;top:12px;right:12px;bottom:12px;border-radius:6px}
.product-info{position:absolute;top:1220px;width:233px;text-align:center}
.stars{color:var(--blue);font-size:12px;letter-spacing:1px}
.product-name{font-size:16px;color:var(--ink);line-height:23px;margin-top:8px;text-transform:uppercase}
.price{font-size:13px;color:var(--orange);margin-top:3px}
.price s{color:#555;margin-right:4px}

/* about */
.about{position:absolute;left:0;top:1395px;width:1200px;height:586px;background:var(--grey-bg)}
.about-photo{position:absolute;left:113px;top:86px;width:447px;height:413px;background:linear-gradient(135deg,#2a3442 0%,#3f5a78 45%,#8fb4d8 60%,#3a2c22 100%)}
.about-title{position:absolute;left:600px;top:100px;font-size:32px;font-weight:700}
.about-title .o{color:var(--orange)}.about-title .b{color:var(--blue)}
.about p{position:absolute;left:600px;top:172px;width:500px;font-size:14px;line-height:30px;color:var(--text)}

/* benefits */
.benefit-num{position:absolute;width:102px;height:102px;border-radius:50%;background:var(--orange);color:var(--white);font-size:44px;font-weight:700;display:flex;align-items:center;justify-content:center}
.benefit{position:absolute;width:310px}
.benefit h3{font-size:16px;font-weight:500;color:var(--ink);letter-spacing:.3px}
.benefit p{font-size:14px;line-height:30px;margin-top:9px;color:var(--text)}
.benefit.left{text-align:right}
.benefit.center{text-align:center}
.hub-brand{position:absolute;left:610px;top:2360px;transform:translate(-50%,-50%);color:var(--white);font-size:18px;font-weight:700;display:flex;align-items:center;gap:8px}

/* contact */
.touch{position:absolute;left:0;top:2889px;width:1200px;height:520px;background:linear-gradient(120deg,#0e56b8 0%,#1c6bd1 50%,#0c4fa8 100%)}
.touch-glow{position:absolute;inset:0;background:radial-gradient(ellipse at 62% 55%,rgba(120,180,255,.35),transparent 55%)}
.touch h2{position:absolute;left:0;top:78px;width:1200px;text-align:center;color:var(--white);font-size:32px;font-weight:700}
.touch p{position:absolute;left:160px;top:150px;width:880px;text-align:center;color:var(--white);font-size:15px;line-height:30px}

/* footer */
.footer-art{position:absolute;left:0;top:3250px;width:1200px;height:473px}
.footer-nav{position:absolute;left:0;top:3552px;width:1200px;font-size:14px;font-weight:700;color:var(--white)}
.footer-nav span{position:absolute;white-space:nowrap}
.social{position:absolute;left:0;top:3607px;width:1200px;height:44px;background:var(--darker);font-size:13px;color:var(--white)}
.social span{position:absolute;top:14px}
.copyright{position:absolute;left:0;top:3672px;width:1200px;text-align:center;font-size:14px;color:#cfcfcf;letter-spacing:.3px}
</style>
</head>
<body>

<!-- Hero -->
<svg class="hero-art" viewBox="0 0 1200 700">
  <defs>
    <linearGradient id="heroGrad" x1="0" y1="0" x2="1" y2="1">
      <stop offset="0" stop-color="#1b222c"/>
      <stop offset=".55" stop-color="#3b4553"/>
      <stop offset=".8" stop-color="#5a5f66"/>
      <stop offset="1" stop-color="#2a2e35"/>
    </linearGradient>
    <radialGradient id="spark" cx=".7" cy=".78" r=".14">
      <stop offset="0" stop-color="#f3c46a" stop-opacity=".8"/>
      <stop offset="1" stop-color="#f3c46a" stop-opacity="0"/>
    </radialGradient>
  </defs>
  <g role="img" aria-label="Laser cutting head shooting sparks onto a steel sheet">
    <path d="M0,0 H1200 V500 C1000,640 520,665 0,578 Z" fill="url(#heroGrad)"/>
    <path d="M0,0 H1200 V500 C1000,640 520,665 0,578 Z" fill="url(#spark)"/>
  </g>
  <path d="M0,578 C520,665 1000,640 1200,500 V545 C1000,700 520,720 0,592 Z" fill="var(--blue)"/>
</svg>

<svg class="abs" style="left:270px;top:0" width="450" height="40" aria-hidden="true">
  <path d="M20,0 H450 V40 H0 Z" fill="#ffffff"/>
</svg>
<div class="topbar">
  <div class="contact" style="left:330px">
    <svg width="11" height="11" viewBox="0 0 24 24"><path d="M6.6 10.8a15 15 0 0 0 6.6 6.6l2.2-2.2c.3-.3.7-.4 1-.2 1.1.4 2.3.6 3.6.6.6 0 1 .4 1 1V20c0 .6-.4 1-1 1A17 17 0 0 1 3 4c0-.6.4-1 1-1h3.5c.6 0 1 .4 1 1 0 1.3.2 2.5.6 3.6.1.3 0 .7-.2 1z" fill="var(--orange)"/></svg>
    +31(0)201234567
  </div>
  <div class="contact" style="left:493px">
    <svg width="12" height="10" viewBox="0 0 24 18"><rect x="1" y="1" width="22" height="16" rx="2" fill="none" stroke="var(--orange)" stroke-width="2.5"/><path d="M2 2l10 8 10-8" fill="none" stroke="var(--orange)" stroke-width="2.5"/></svg>
    info@flintboro-mail.com
  </div>
  <div class="search">Search Product....
    <svg width="12" height="12" viewBox="0 0 24 24"><circle cx="10" cy="10" r="7" fill="none" stroke="#444" stroke-width="3"/><path d="M15 15l7 7" stroke="#444" stroke-width="3"/></svg>
  </div>
  <div class="user-tools">
    <svg width="10" height="12" viewBox="0 0 20 24"><circle cx="10" cy="6" r="5" fill="#222"/><path d="M0 24c0-7 4-10 10-10s10 3 10 10z" fill="#222"/></svg>
    <span>|</span>
    <svg width="13" height="12" viewBox="0 0 24 22"><path d="M12 22L2 12A6 6 0 0 1 12 3a6 6 0 0 1 10 9z" fill="#222"/></svg>
    <span>|</span>
    <svg width="13" height="12" viewBox="0 0 24 22"><path d="M0 1h4l3 12h13l3-9H6" fill="none" stroke="#222" stroke-width="2.5"/><circle cx="9" cy="19" r="2" fill="#222"/><circle cx="19" cy="19" r="2" fill="#222"/></svg>
  </div>
</div>

<div class="brand" style="left:150px;top:56px;color:var(--white);font-size:20px"><span class="dot"></span>FLINTBORO</div>

<nav class="main-nav">
  <a style="left:400px">HOME</a>
  <a style="left:483px">ABOUT US</a>
  <a style="left:596px">PRODUCTS</a>
  <a style="left:714px">BENIFITS</a>
  <a style="left:823px">BLOGS</a>
</nav>
<a class="btn" style="left:922px;top:59px;width:165px;height:45px;font-size:16px">CONTACT US</a>

<h1 class="hero-title">Simple Welding of Steel and Aluminum Get Great Results With Tools That Work</h1>
<a class="btn" style="left:113px;top:428px;width:165px;height:43px;font-size:16px">SHOP NOW</a>
<div class="slider-dots">
  <span style="top:274px"></span>
  <span class="on" style="top:295px"></span>
  <span style="top:320px"></span>
  <span style="top:343px"></span>
  <span style="top:366px"></span>
</div>

<!-- Products -->
<h2 class="section-title" style="top:772px"><span class="o">OUR</span> <span class="b">PRODUCTS</span></h2>
<div class="rule" style="left:577px;top:818px"></div>
<div class="shipping">FREE SHIPPING FROM € 30.00</div>

<div class="product-card" style="left:94px"><div class="photo" role="img" aria-label="Black auto-darkening welding helmet" style="background:radial-gradient(circle at 50% 50%,#55575c 0%,#2a2b2e 45%,#fafafa 70%)"></div></div>
<div class="product-card" style="left:354px"><div class="photo" role="img" aria-label="Grey and blue welding machine" style="background:radial-gradient(circle at 50% 50%,#8a96a8 0%,#3f6fc2 45%,#fafafa 72%)"></div></div>
<div class="product-card" style="left:613px"><div class="photo" role="img" aria-label="Red welding machine" style="background:radial-gradient(circle at 50% 50%,#5a2226 0%,#c82a2a 42%,#fafafa 70%)"></div></div>
<div class="product-card" style="left:872px"><div class="photo" role="img" aria-label="Pair of black leather welding gloves" style="background:radial-gradient(circle at 50% 50%,#3a3a34 0%,#1e1e1c 45%,#fafafa 72%)"></div></div>

<div class="product-info" style="left:94px"><div class="stars">★★★★★</div><div class="product-name">Welding Helmet 180<br>Degrees View</div><div class="price">€109,00</div></div>
<div class="product-info" style="left:354px"><div class="stars">★★★★★</div><div class="product-name" style="margin-top:10px">ARC-1900</div><div class="price" style="margin-top:12px">€745,00</div></div>
<div class="product-info" style="left:613px"><div class="stars">★★★★★</div><div class="product-name">ARC-210X</div><div class="price" style="margin-top:12px"><s>€ 845.00</s>€ 795.00</div></div>
<div class="product-info" style="left:872px"><div class="stars">★★★★★</div><div class="product-name">Welding Gloves<br>Black</div><div class="price">€ 22.40</div></div>

<!-- About -->
<section class="about">
  <div class="about-photo" role="img" aria-label="Welder in a mask working on steel with bright sparks"></div>
  <h2 class="about-title"><span class="o">ABOUT</span> <span class="b">FLINTBORO</span></h2>
  <div class="rule" style="left:600px;top:144px"></div>
  <p>Lorem ipsum dolor sit amet, consectetur adipiscing elit, sed do eiusmod tempor incididunt ut labore et dolore magna aliqua. Ut enim ad minim veniam, quis nostrud exercitation ullamco laboris nisi ut aliquip ex ea commodo consequat. Duis aute irure dolor in reprehenderit in voluptate velit esse cillum dolore eu fugiat nulla pariatur. Excepteur sint occaecat cupidatat non proident, sunt in culpa qui officia deserunt mollit anim id est laborum. Lorem ipsum dolor sit amet, consectetur adipiscing elit, sed do eiusmod tempor incididunt ut labore et dolore magna aliqua.</p>
  <a class="btn" style="left:600px;top:434px;width:168px;height:43px;font-size:16px">SHOP NOW</a>
</section>

<!-- Benefits -->
<h2 class="section-title" style="top:2059px"><span class="o">OUR</span> <span class="b">BENEFITS</span></h2>
<div class="rule" style="left:577px;top:2104px"></div>

<svg class="abs" style="left:0;top:2100px" width="1200" height="560" aria-hidden="true">
  <g stroke="var(--orange)" stroke-width="1.2" stroke-dasharray="3 3" fill="none">
    <line x1="328" y1="70" x2="610" y2="260"/>
    <line x1="857" y1="70" x2="610" y2="260"/>
    <line x1="328" y1="423" x2="610" y2="260"/>
    <line x1="857" y1="423" x2="610" y2="260"/>
    <line x1="610" y1="260" x2="610" y2="526"/>
  </g>
  <circle cx="610" cy="260" r="155" fill="var(--blue-light)"/>
  <circle cx="610" cy="260" r="116" fill="var(--blue)"/>
</svg>
<div class="hub-brand"><span style="width:14px;height:14px;border-radius:50%;background:var(--orange);display:inline-block"></span>FLINTBORO</div>

<div class="benefit-num" style="left:277px;top:2119px">05</div>
<div class="benefit-num" style="left:806px;top:2119px">01</div>
<div class="benefit-num" style="left:277px;top:2472px">04</div>
<div class="benefit-num" style="left:806px;top:2472px">02</div>
<div class="benefit-num" style="left:558px;top:2575px">03</div>

<div class="benefit left" style="left:66px;top:2235px"><h3>LOREM IPSUM DOLOR SIT</h3><p>Lorem ipsum dolor sit amet, consectetur adip-iscing elit, sed do eiusmod tempor incididunt ut labore et dolore magna aliqua.</p></div>
<div class="benefit" style="left:824px;top:2235px"><h3>LOREM IPSUM DOLOR SIT</h3><p>Lorem ipsum dolor sit amet, consectetur adip-iscing elit, sed do eiusmod tempor incididunt ut labore et dolore magna aliqua.</p></div>
<div class="benefit left" style="left:66px;top:2587px"><h3>LOREM IPSUM DOLOR SIT</h3><p>Lorem ipsum dolor sit amet, consectetur adip-iscing elit, sed do eiusmod tempor incididunt ut labore et dolore magna aliqua.</p></div>
<div class="benefit" style="left:824px;top:2587px"><h3>LOREM IPSUM DOLOR SIT</h3><p>Lorem ipsum dolor sit amet, consectetur adip-iscing elit, sed do eiusmod tempor incididunt ut labore et dolore magna aliqua.</p></div>
<div class="benefit center" style="left:454px;top:2689px"><h3>LOREM IPSUM DOLOR SIT</h3><p>Lorem ipsum dolor sit amet, consectetur adip-iscing elit, sed do eiusmod tempor incididunt ut labore et dolore magna aliqua.</p></div>

<!-- Get in touch -->
<section class="touch" role="img" aria-label="Blue-toned welding scene with sparks in the background">
  <div class="touch-glow"></div>
  <h2>GET IN TOUCH</h2>
  <p>Lorem ipsum dolor sit amet, consectetur adipiscing elit, sed do eiusmod tempor incididunt ut labore et dolore magna aliqua. Ut enim ad minim veniam, quis nostrud exercitation ullamco laboris nisi ut aliquip ex ea commodo consequat. Duis aute irure dolor in reprehenderit in voluptate velit esse cillum dolore eu fugiat nulla pariatur. Excepteur sint occaecat cupidatat non proi-dent, sunt in culpa qui officia deserunt mollit anim id est laborum</p>
  <a class="btn" style="left:516px;top:286px;width:166px;height:43px;font-size:16px">GET A QUOTE</a>
</section>

<!-- Footer -->
<svg class="footer-art" viewBox="0 0 1200 473" aria-hidden="true">
  <path d="M0,143 C320,15 880,20 1200,228 V473 H0 Z" fill="var(--orange)"/>
  <path d="M0,158 C360,55 860,62 1200,262 V473 H0 Z" fill="var(--dark)"/>
</svg>
<div class="brand" style="left:0;top:3455px;width:1200px;justify-content:center;color:var(--white);font-size:22px"><span class="dot"></span>FLINTBORO</div>

<nav class="footer-nav">
  <span style="left:284px">HOME</span>
  <span style="left:364px">|</span>
  <span style="left:408px">ABOUT US</span>
  <span style="left:517px">|</span>
  <span style="left:561px">PRODUCTS</span>
  <span style="left:677px">|</span>
  <span style="left:719px">BENIFITS</span>
  <span style="left:825px">|</span>
  <span style="left:868px">BLOGS</span>
</nav>

<div class="social">
  <span style="left:291px">SPARKNET</span>
  <span style="left:484px">CHIRPLY</span>
  <span style="left:660px">LINKWAVE</span>
  <span style="left:840px">SNAPFRAME</span>
</div>

<div class="copyright">© COPYRIGHTS 2021 FLINTBORO &nbsp;&nbsp;| &nbsp;&nbsp;&nbsp;ALL RIGHTS RESERVED.</div>

</body>
</html>
```